Tellmora Corporate Stationery

Look for design of all new corporate stationery for an existing insurance broking business that is going through a redesign and move from older partners to younger family members. New Logo is attached. Company is Brisbane based.
Colours in the Logo is Hex #43bed8 and website features a lot of hex #17b8d8. Website front page "A plan to protect you" - headline. "Professional and Individual advice to protect your greatest assets" - tagline.

Stationery required: Business Cards, Letter head, Thank-you cards, Birthday cards, Presentation folders, With Compliment slips and a powerpoint template. We also would like to send a card to all customers with the something along of the lines of "something new".

Target Market(s)

Customers of Insurance business looking at superannuation, life and income protection insurance, investment advice and wills

Industry/Entity Type

Insurance Broker

Font styles to use
Other font styles liked:
• same as logo

Requirements
Must have
• The above designs for new stationery for the new business including:
• Business Cards, Letter head, Thank-you cards, Birthday cards, Presentation folders, With Compliment slips and a powerpoint template. We also would like to send a card to all customers with the something along of the lines of "something new".
Nice to have
• It is a new look - long time family business being passed to next generation - big focus on advice for YOU, individual advice etc..

```html
<!DOCTYPE html>
<html lang="en">
<head>
<meta charset="utf-8">
<title>Tellmora Letterhead</title>
<link href="https://fonts.googleapis.com/css2?family=Montserrat:wght@300;500&family=Roboto+Condensed:wght@400&display=swap" rel="stylesheet">
<style>
  :root {
    --backdrop: #bfe7e9;
    --paper: #ffffff;
    --brand-blue: #43bed8;
    --ink-grey: #8a8d90;
    --footer-ink: #4a4d50;
    --watermark: #eef8fa;
  }
  * { margin: 0; padding: 0; box-sizing: border-box; }
  html, body {
    width: 1200px; height: 784px; overflow: hidden;
    background: var(--backdrop);
  }
  .canvas {
    position: relative; width: 1200px; height: 784px;
    display: flex; align-items: center; justify-content: center;
  }
  .letterhead {
    position: relative; width: 510px; height: 722px;
    background: var(--paper);
    box-shadow: 0 4px 14px rgba(40, 120, 130, 0.18);
    overflow: hidden;
  }
  .brand {
    position: absolute; top: 34px; left: 36px;
    display: flex; align-items: center; gap: 9px;
  }
  .brand-dot {
    width: 22px; height: 22px; border-radius: 50%;
    background: var(--brand-blue);
  }
  .brand-name {
    font-family: "Montserrat", sans-serif; font-weight: 500;
    font-size: 19px; letter-spacing: 2px; text-transform: uppercase;
    color: var(--brand-blue);
  }
  .tagline {
    position: absolute; top: 92px; right: 36px; text-align: right;
    font-family: "Montserrat", sans-serif; font-weight: 300;
    text-transform: uppercase;
  }
  .tagline-headline {
    font-size: 9px; letter-spacing: 1.2px; color: var(--brand-blue);
    margin-bottom: 4px;
  }
  .tagline-sub {
    font-size: 6px; letter-spacing: 0.8px; color: var(--ink-grey);
  }
  .watermark {
    position: absolute; left: 70px; bottom: 40px;
    width: 230px; height: 230px;
  }
  .contact-bar {
    position: absolute; left: 22px; right: 22px; bottom: 14px;
    display: flex; align-items: center; gap: 12px;
    font-family: "Roboto Condensed", sans-serif; font-size: 8px;
    color: var(--footer-ink); white-space: nowrap;
  }
  .contact-item { display: flex; align-items: center; gap: 4px; }
  .contact-icon { width: 9px; height: 9px; flex: none; }
</style>
</head>
<body>
<main class="canvas">
  <article class="letterhead">
    <header class="brand">
      <span class="brand-dot"></span>
      <span class="brand-name">Tellmora</span>
    </header>

    <section class="tagline">
      <p class="tagline-headline">A plan to protect you</p>
      <p class="tagline-sub">Professional and individual advice to protect your greatest assets</p>
    </section>

    <svg class="watermark" viewBox="0 0 230 230" aria-hidden="true">
      <circle cx="115" cy="115" r="100" fill="none" stroke="var(--watermark)" stroke-width="22"/>
    </svg>

    <footer class="contact-bar">
      <span class="contact-item">
        <svg class="contact-icon" viewBox="0 0 10 10"><circle cx="5" cy="5" r="5" fill="var(--brand-blue)"/><path d="M5 2.2a1.8 1.8 0 0 0-1.8 1.8C3.2 5.4 5 7.8 5 7.8S6.8 5.4 6.8 4A1.8 1.8 0 0 0 5 2.2z" fill="#fff"/></svg>
        Example Lane, Suite 200 Brisbane, QLD 4000
      </span>
      <span class="contact-item">
        <svg class="contact-icon" viewBox="0 0 10 10"><circle cx="5" cy="5" r="5" fill="var(--brand-blue)"/><path d="M3.4 2.6l1 1-.5.7a4 4 0 0 0 1.8 1.8l.7-.5 1 1-.7.8C5 7.2 2.8 5 2.6 3.3z" fill="#fff"/></svg>
        (000) 000-4518
      </span>
      <span class="contact-item">
        <svg class="contact-icon" viewBox="0 0 10 10"><circle cx="5" cy="5" r="5" fill="var(--brand-blue)"/><rect x="2.8" y="3.6" width="4.4" height="3" fill="#fff"/><rect x="3.6" y="2.4" width="2.8" height="1.4" fill="#fff"/></svg>
        (000) 000-6392
      </span>
      <span class="contact-item">
        <svg class="contact-icon" viewBox="0 0 10 10"><circle cx="5" cy="5" r="5" fill="var(--brand-blue)"/><path d="M3 7l4-4M4 3h3v3" stroke="#fff" stroke-width="1" fill="none"/></svg>
        www.tellmoragroup.com
      </span>
    </footer>
  </article>
</main>
</body>
</html>
```